Storefront signage for Physio clinic

We need a design for our storefront windows at our physiotherapy & Pilates clinic.

The design should be modern and include our logo, website url and services (physiotherapy, pilates, massage).

Some inspirational exercise/pilates/recovery quotes may be included and I would like to see the use of sport/pilates/injury related stock images. I have attached a few examples of what we want (images numbered 1-5). And I have attached our current design and photo of the outside of our clinic.

In the attached images there is also a pdf with measurments of our window panels. We require signage for the areas marked 1-10. As you can see on our current signage, you don't need to have a separate image for each panel, these can flow onto each other.
Updates

Industry/Entity Type

Clinic

Colors
85acd3
3377b5
3277b5
e8e8e8
c3c3c3
9d9d9d
848484
7f7f7f

Requirements
Must have
• Stock images related to sports, physiotherapy and pilates
• Ideally these images should be in greyscale and blend in with the rest of the panel which should include colours.
• I would like to see for example a runner, a weightlifter, someone doing pilates, someone with back pain (not necessarily all of these).
Should not have
• I want a creative, modern, up market design, not just a standard recycled template.

```html
<!DOCTYPE html>
<html lang="en">
<head>
<meta charset="utf-8">
<title>Riverbend Physio – Window Signage</title>
<link rel="stylesheet" href="https://fonts.googleapis.com/css2?family=Rubik:wght@400;500;700&display=swap">
<style>
:root{
  --navy:#1c3566;
  --royal:#1d4f9c;
  --mid:#3277b5;
  --sky:#85acd3;
  --cyan:#1b9bd8;
  --teal:#0f6e86;
  --white:#ffffff;
  --page:#e8e8e8;
  --grey-light:#c3c3c3;
  --grey:#9d9d9d;
  --grey-dark:#7f7f7f;
}
*{box-sizing:border-box;margin:0;padding:0}
html,body{width:1200px;height:1200px;overflow:hidden}
body{background:var(--page);font-family:"Rubik",sans-serif;position:relative}
.panel{position:absolute;overflow:hidden}
.photo{position:absolute;inset:0}
.poster-left{left:49px;top:166px;width:556px;height:388px}
.poster-right{left:619px;top:166px;width:531px;height:388px}
.poster-left .photo{background:linear-gradient(120deg,#5a5a5a 0%,#c9c9c9 40%,#8a8a8a 65%,#e2e2e2 100%)}
.poster-right .photo{background:linear-gradient(100deg,#d8d8d8 0%,#f2f2f2 35%,#a9a9a9 60%,#e6e6e6 100%)}
.deco{position:absolute;inset:0}
.base-strip{position:absolute;left:0;right:0;bottom:0;height:6px;background:var(--navy)}
.brand{position:absolute;display:flex;align-items:center;gap:5px;font-weight:500;font-size:12px;color:var(--mid);letter-spacing:.3px}
.brand-dot{width:12px;height:12px;border-radius:50%;background:var(--mid)}
.headline{position:absolute;font-weight:700;font-size:27px;line-height:.96;color:var(--royal);letter-spacing:.3px}
.tagline{position:absolute;font-size:11.5px;color:var(--mid)}
.cta{position:absolute;height:18px;background:var(--royal);color:var(--white);font-size:8px;font-weight:700;display:flex;align-items:center;justify-content:center;letter-spacing:.4px}
.services{position:absolute;display:flex;gap:5px;list-style:none}
.services li{width:109px;height:15px;color:var(--white);font-size:8px;padding-left:6px;display:flex;align-items:center}
.services li:nth-child(1){background:var(--sky)}
.services li:nth-child(2){background:var(--mid)}
.services li:nth-child(3){background:var(--royal)}
.services li:nth-child(4){background:var(--navy)}
.url{position:absolute;font-size:7.5px;font-weight:500;color:var(--navy)}
.poster-right .url{color:var(--white)}
.door{left:374px;top:686px;width:473px;height:390px;background:var(--white)}
.door-col{position:absolute;top:0;bottom:0}
.col-a{left:0;width:130px;background:linear-gradient(var(--sky) 0 189px,var(--navy) 189px)}
.col-d{left:341px;width:132px;background:linear-gradient(var(--navy) 0 189px,var(--sky) 189px)}
.door-split{position:absolute;left:237px;top:0;bottom:0;width:1px;background:#dcdcdc}
.door-label{position:absolute;top:14px;font-size:7.5px;font-weight:700;color:var(--grey-dark)}
.door-mark{position:absolute;left:211px;top:168px;width:52px;height:52px;border-radius:50%;background:var(--sky)}
.door-photo{position:absolute;top:117px;width:125px;height:155px}
.phone{position:absolute;left:0;width:130px;top:338px;text-align:center;color:var(--white);font-size:9px;font-weight:500}
.phone svg{display:block;margin:0 auto 3px}
.address{position:absolute;left:341px;width:132px;top:340px;text-align:center;color:var(--white);font-size:6.5px;line-height:1.35;font-weight:500}
</style>
</head>
<body>

<section class="panel poster-left">
  <div class="photo" role="img" aria-label="Greyscale photo of an athlete holding a sore knee"></div>
  <svg class="deco" width="556" height="388" viewBox="0 0 556 388">
    <defs>
      <linearGradient id="tealWash" x1="0" y1="0" x2="1" y2="1">
        <stop offset="0" stop-color="#0e5f73"/><stop offset="1" stop-color="#1b9bd8"/>
      </linearGradient>
    </defs>
    <polygon points="0,0 290,0 0,290" fill="url(#tealWash)" opacity=".9"/>
    <g fill="#fff" transform="translate(119 152) rotate(45)">
      <rect x="-150" y="-52" width="300" height="104"/>
      <rect x="-52" y="-150" width="104" height="300"/>
      <rect x="-95" y="-62" width="40" height="10"/>
      <rect x="60" y="52" width="50" height="10"/>
    </g>
    <line x1="210" y1="18" x2="245" y2="-14" stroke="#fff" stroke-width="2"/>
    <line x1="22" y1="300" x2="40" y2="282" stroke="#fff" stroke-width="2"/>
  </svg>
  <div class="brand" style="left:439px;top:40px"><span class="brand-dot"></span>Riverbend Physio</div>
  <h1 class="headline" style="left:56px;top:98px">GOOD<br>THINGS</h1>
  <p class="tagline" style="left:57px;top:159px">come to those who sweat...</p>
  <div class="cta" style="left:58px;top:174px;width:121px">ENROLL NOW !</div>
  <ul class="services" style="left:49px;top:306px">
    <li>PHYSIOTHERAPY</li><li>PILATES</li><li>MASSAGE</li><li>WORK REHABILITATION</li>
  </ul>
  <p class="url" style="left:207px;top:368px">www.riverbendphysio.com.au</p>
  <div class="base-strip"></div>
</section>

<section class="panel poster-right">
  <div class="photo" role="img" aria-label="Greyscale photo of a woman stretching over a Pilates ball in a studio"></div>
  <svg class="deco" width="531" height="388" viewBox="0 0 531 388">
    <defs>
      <linearGradient id="cyanWash" x1="0" y1="0" x2="0" y2="1">
        <stop offset="0" stop-color="#1b9bd8"/><stop offset="1" stop-color="#0f6e86"/>
      </linearGradient>
    </defs>
    <polygon points="531,90 531,388 290,388" fill="url(#cyanWash)" opacity=".92"/>
    <g fill="#fff" transform="translate(419 236) rotate(45)">
      <rect x="-145" y="-50" width="290" height="100"/>
      <rect x="-50" y="-145" width="100" height="290"/>
      <rect x="-100" y="50" width="45" height="10"/>
    </g>
    <line x1="300" y1="372" x2="330" y2="344" stroke="#fff" stroke-width="2"/>
  </svg>
  <div class="brand" style="left:407px;top:40px"><span class="brand-dot"></span>Riverbend Physio</div>
  <ul class="services" style="left:34px;top:65px">
    <li>PHYSIOTHERAPY</li><li>PILATES</li><li>MASSAGE</li><li>WORK REHABILITATION</li>
  </ul>
  <h1 class="headline" style="left:355px;top:202px">PUSH<br>HARDER</h1>
  <p class="tagline" style="left:355px;top:264px">for a different tomorrow...</p>
  <div class="cta" style="left:355px;top:279px;width:122px">ENROLL NOW !</div>
  <p class="url" style="left:208px;top:368px">www.riverbendphysio.com.au</p>
  <div class="base-strip"></div>
</section>

<section class="panel door">
  <div class="door-col col-a"></div>
  <div class="door-col col-d"></div>
  <div class="door-split"></div>
  <span class="door-label" style="left:184px">EDOOR</span>
  <span class="door-label" style="left:260px">DOOR</span>
  <div class="door-mark"></div>

  <svg class="door-photo" style="left:4px" viewBox="0 0 125 155" role="img" aria-label="Greyscale photo of a woman in a stretching pose">
    <defs>
      <linearGradient id="greyA" x1="0" y1="0" x2="1" y2="1">
        <stop offset="0" stop-color="#e4e4e4"/><stop offset="1" stop-color="#7f7f7f"/>
      </linearGradient>
    </defs>
    <g fill="url(#greyA)" transform="translate(62 77) rotate(45)">
      <rect x="-70" y="-28" width="140" height="56"/>
      <rect x="-28" y="-70" width="56" height="140"/>
    </g>
  </svg>

  <svg class="door-photo" style="left:344px" viewBox="0 0 125 155" role="img" aria-label="Greyscale photo of a man holding a painful shoulder">
    <defs>
      <linearGradient id="greyB" x1="1" y1="0" x2="0" y2="1">
        <stop offset="0" stop-color="#c3c3c3"/><stop offset="1" stop-color="#848484"/>
      </linearGradient>
    </defs>
    <g fill="url(#greyB)" transform="translate(62 77) rotate(45)">
      <rect x="-70" y="-28" width="140" height="56"/>
      <rect x="-28" y="-70" width="56" height="140"/>
    </g>
  </svg>

  <div class="phone">
    <svg width="14" height="12" viewBox="0 0 14 12" aria-hidden="true">
      <path d="M1 4 Q7 0 13 4 L12 6 L9.5 5 L9.5 3.5 Q7 2.8 4.5 3.5 L4.5 5 L2 6 Z" fill="#fff"/>
      <rect x="3" y="6" width="8" height="5.5" rx="1" fill="#fff"/>
    </svg>
    02 5550 1234
  </div>
  <p class="address">Shop #12, 40 Harbour St.<br>Riverbend,<br>www.riverbendphysio.com.au</p>
</section>

</body>
</html>
```